Presentation Of Our Epidemiology Consulting Framework

We need a slide deck (png files) for PowerPoint that describes our organization and type of clients we serve, and our 6 phase framework that explains how we work with clients. Please use the minimum amount of text on each slide.  We want a more visual display of how to work with us. We want it to look very similar to our brochure.  We want to also have a few extra branded slides without text that can be used as a template if we decide to add to the deck later or create a new slide deck.
Colors
#56588C
#F28444
#F2E088
#F24C27
#ODODOD

```html
<!DOCTYPE html>
<html lang="en">
<head>
<meta charset="utf-8">
<title>Epidemiology Consulting Framework – Slide Deck</title>
<link href="https://fonts.googleapis.com/css2?family=Exo+2:wght@500;600&family=Nunito+Sans:wght@400;600&display=swap" rel="stylesheet">
<style>
  :root{
    --page:#ffffff;
    --navy-deep:#100f28;
    --navy:#1c1a45;
    --indigo:#2e2b6a;
    --violet:#56588c;
    --orange:#f28444;
    --red:#f24c27;
    --white:#ffffff;
    --muted:#d4d3e6;
    --line:rgba(120,118,190,.45);
  }
  *{box-sizing:border-box;margin:0;padding:0}
  html,body{width:1029px;height:1200px;overflow:hidden;background:var(--page)}
  body{position:relative;font-family:"Nunito Sans",Arial,sans-serif;color:var(--white)}
  .slide{position:absolute;width:438px;height:246px;overflow:hidden;
    background:linear-gradient(120deg,var(--navy-deep) 0%,var(--navy) 55%,var(--indigo) 100%)}
  .col-left{left:58px}.col-right{left:534px}
  .brand{position:absolute;font-family:"Nunito Sans",Arial,sans-serif;font-weight:600;font-size:16px;color:var(--orange);white-space:nowrap;line-height:1}
  .heading{position:absolute;font-family:"Exo 2",Arial,sans-serif;font-weight:500;text-transform:uppercase;line-height:1;white-space:nowrap;letter-spacing:.3px}
  .accent{color:var(--red)}
  .sub{position:absolute;font-weight:600;white-space:nowrap;line-height:1}
  .tagline{position:absolute;font-family:"Nunito Sans",Arial,sans-serif;font-weight:400;font-size:12.5px;white-space:nowrap}
  .photo{position:absolute}
  .card{position:absolute;border:1px solid var(--line);background:rgba(16,15,40,.35);text-align:center;
    display:flex;flex-direction:column;align-items:center;font-size:7px;line-height:1.35;color:var(--muted)}
  .card svg{width:20px;height:20px;color:var(--red);margin-bottom:9px;flex:none}
  .list-item{position:absolute;height:21px;border:1px solid var(--line);background:rgba(16,15,40,.45);
    display:flex;align-items:center;gap:8px;padding-left:8px;font-size:7.5px;color:var(--white);white-space:nowrap}
  .list-item svg{width:11px;height:11px;color:var(--red);flex:none}
  .rule{position:absolute;background:var(--red)}
  .step{position:absolute;top:186px;height:60px;text-align:center;font-size:7.5px;line-height:1.45;color:var(--muted);padding-top:28px;white-space:nowrap}
  .step-badge{position:absolute;top:-17px;left:50%;width:34px;height:34px;margin-left:-17px;border-radius:50%;
    background:var(--red);border:2px solid var(--navy-deep);display:flex;align-items:center;justify-content:center}
  .step-badge svg{width:15px;height:15px;color:var(--white)}
  .step + .step{border-left:1px solid var(--line)}
</style>
</head>
<body>
<svg width="0" height="0" style="position:absolute">
  <symbol id="i-target" viewBox="0 0 24 24"><g fill="none" stroke="currentColor" stroke-width="1.5"><circle cx="12" cy="12" r="9"/><circle cx="12" cy="12" r="5"/><circle cx="12" cy="12" r="1.5"/></g></symbol>
  <symbol id="i-bulb" viewBox="0 0 24 24"><g fill="none" stroke="currentColor" stroke-width="1.5"><path d="M8 14a6 6 0 1 1 8 0c-1 1-1.5 2-1.5 3h-5c0-1-.5-2-1.5-3z"/><path d="M9.5 20h5"/></g></symbol>
  <symbol id="i-route" viewBox="0 0 24 24"><g fill="none" stroke="currentColor" stroke-width="1.5"><circle cx="5" cy="6" r="2"/><circle cx="19" cy="12" r="2"/><circle cx="5" cy="18" r="2"/><path d="M7 6h10a3 3 0 0 1 0 6H7a3 3 0 0 0 0 6h10"/></g></symbol>
  <symbol id="i-people" viewBox="0 0 24 24"><g fill="none" stroke="currentColor" stroke-width="1.5"><circle cx="7" cy="8" r="3"/><circle cx="17" cy="8" r="3"/><path d="M2 19a5 5 0 0 1 10 0M12 19a5 5 0 0 1 10 0"/></g></symbol>
  <symbol id="i-chart" viewBox="0 0 24 24"><g fill="none" stroke="currentColor" stroke-width="1.5"><rect x="3" y="4" width="18" height="13"/><path d="M7 14v-3M11 14V9M15 14v-5M12 17v3M8 20h8"/></g></symbol>
  <symbol id="i-gear" viewBox="0 0 24 24"><g fill="none" stroke="currentColor" stroke-width="1.5"><circle cx="12" cy="12" r="3"/><circle cx="12" cy="12" r="7" stroke-dasharray="3 2"/></g></symbol>
  <symbol id="i-check" viewBox="0 0 24 24"><g fill="none" stroke="currentColor" stroke-width="1.5"><circle cx="12" cy="12" r="9"/><path d="M8 12l3 3 5-6"/></g></symbol>
  <symbol id="i-chat" viewBox="0 0 24 24"><g fill="none" stroke="currentColor" stroke-width="1.5"><path d="M4 4h16v11H10l-4 4v-4H4z"/><path d="M8 8h8M8 11h5"/></g></symbol>
  <symbol id="i-eye" viewBox="0 0 24 24"><g fill="none" stroke="currentColor" stroke-width="1.5"><path d="M2 12s4-6 10-6 10 6 10 6-4 6-10 6S2 12 2 12z"/><circle cx="12" cy="12" r="3"/></g></symbol>
  <symbol id="i-globe" viewBox="0 0 24 24"><g fill="none" stroke="currentColor" stroke-width="1.5"><circle cx="12" cy="12" r="9"/><path d="M3 12h18M12 3c3 3 3 15 0 18M12 3c-3 3-3 15 0 18"/></g></symbol>
  <symbol id="i-hands" viewBox="0 0 24 24"><g fill="none" stroke="currentColor" stroke-width="1.5"><path d="M2 9l4-3 5 3 4-2 7 4-5 5-4-2-3 2z"/></g></symbol>
</svg>

<!-- Title -->
<section class="slide col-left" style="top:55px">
  <div class="photo" role="img" aria-label="Portrait of the consultant in a dark blazer" style="left:282px;top:0;width:156px;height:246px;background:linear-gradient(160deg,#5b58a8 0%,#3a3780 45%,#1f1d4a 100%)"></div>
  <div class="brand" style="left:35px;top:32px;font-size:18px">Dr Navela Rowe</div>
  <div class="heading" style="left:33px;top:89px;font-size:23px;line-height:30px">Transforming<br><span class="accent">Health Data<br>Into Community</span><br>Impact</div>
</section>

<!-- Discovery -->
<section class="slide col-right" style="top:55px">
  <div class="brand" style="left:23px;top:22px">Dr Navela Rowe</div>
  <div class="heading" style="left:21px;top:59px;font-size:13px;line-height:17px">Discovery &amp;<br><span class="accent">Vision Alignment</span></div>
  <div class="rule" style="left:166px;top:60px;width:1.5px;height:28px"></div>
  <div class="heading" style="left:185px;top:62px;font-size:11px;line-height:14px">Building the Foundation<br>for Success</div>
  <div class="card" style="left:23px;top:113px;width:93px;height:108px;padding-top:16px"><svg><use href="#i-bulb"/></svg>Deep-dive exploration of<br>your organization's<br>unique challenges and<br>opportunities</div>
  <div class="card" style="left:127px;top:113px;width:93px;height:108px;padding-top:16px"><svg><use href="#i-target"/></svg>Strategic alignment<br>of goals and<br>expectations</div>
  <div class="card" style="left:229px;top:113px;width:93px;height:108px;padding-top:16px"><svg><use href="#i-check"/></svg>Custom-tailored<br>solution design</div>
  <div class="card" style="left:332px;top:113px;width:93px;height:108px;padding-top:16px"><svg><use href="#i-route"/></svg>Clear roadmap<br>development with<br>defined milestones</div>
</section>

<!-- Partnership -->
<section class="slide col-left" style="top:329px">
  <div class="photo" role="img" aria-label="Two business people shaking hands, tinted violet" style="left:220px;top:0;width:218px;height:246px;background:linear-gradient(90deg,rgba(46,43,106,0) 0%,#4b4a8a 45%,#7a79b0 100%)"></div>
  <div class="brand" style="left:21px;top:18px">Dr Navela Rowe</div>
  <div class="heading" style="left:22px;top:52px;font-size:13px">Partnership <span class="accent">Launch</span></div>
  <div class="sub" style="left:22px;top:69px;font-size:8px">SETTING THE STAGE FOR EXCELLENCE</div>
  <div class="list-item" style="left:23px;top:94px;width:183px"><svg><use href="#i-people"/></svg>Formation of dedicated project team</div>
  <div class="list-item" style="left:23px;top:120.5px;width:183px"><svg><use href="#i-route"/></svg>Establishment of collaborative workflow</div>
  <div class="list-item" style="left:23px;top:147px;width:183px"><svg><use href="#i-chart"/></svg>Comprehensive data gathering</div>
  <div class="list-item" style="left:23px;top:173.5px;width:183px"><svg><use href="#i-chart"/></svg>Strategic timeline planning</div>
  <div class="list-item" style="left:23px;top:200px;width:183px"><svg><use href="#i-eye"/></svg>Stakeholder engagement and vision capture</div>
</section>

<!-- Execution -->
<section class="slide col-right" style="top:330px">
  <div class="brand" style="left:17px;top:20px">Dr Navela Rowe</div>
  <div class="rule" style="left:165px;top:14px;width:1.5px;height:27px"></div>
  <div class="heading" style="left:179px;top:15px;font-size:13px">Expert <span class="accent">Execution</span></div>
  <div class="sub" style="left:179px;top:32px;font-size:8px">WHERE SCIENCE MEETS SERVICE</div>
  <div class="photo" role="img" aria-label="City office window with data dashboards and bar charts" style="left:0;top:56px;width:438px;height:130px;background:linear-gradient(100deg,#3b3c66 0%,#5a4a6e 30%,#3a2530 60%,#6b2418 85%,#2a1a28 100%)"></div>
  <div class="step" style="left:0;width:98px"><span class="step-badge"><svg><use href="#i-chart"/></svg></span>In-depth research<br>and analysis</div>
  <div class="step" style="left:98px;width:106px"><span class="step-badge"><svg><use href="#i-chat"/></svg></span>Content development<br>and refinement</div>
  <div class="step" style="left:204px;width:103px"><span class="step-badge"><svg><use href="#i-chart"/></svg></span>Data interpretation<br>and visualization</div>
  <div class="step" style="left:307px;width:131px"><span class="step-badge"><svg><use href="#i-globe"/></svg></span>Plain language translation<br>of complex health information</div>
</section>

<!-- Refinement -->
<section class="slide col-left" style="top:602px">
  <div class="brand" style="left:25px;top:55px;font-size:17px">Dr Navela Rowe</div>
  <div class="heading" style="left:23px;top:98px;font-size:19px;line-height:24px">Collaborative<br><span class="accent">Refinement</span></div>
  <div class="tagline" style="left:24px;top:151px">Ensuring Perfect Alignment</div>
  <div class="card" style="left:215px;top:24px;width:93px;height:81px;padding-top:11px"><svg><use href="#i-chart"/></svg>Presentation of initial<br>frameworks</div>
  <div class="card" style="left:319px;top:50px;width:93px;height:81px;padding-top:14px"><svg><use href="#i-chat"/></svg>Interactive feedback<br>sessions</div>
  <div class="card" style="left:215px;top:116px;width:93px;height:81px;padding-top:13px"><svg><use href="#i-gear"/></svg>Stakeholder input<br>integration</div>
  <div class="card" style="left:319px;top:142px;width:93px;height:81px;padding-top:13px"><svg><use href="#i-check"/></svg>Draft review and<br>optimization</div>
</section>

<!-- Impact -->
<section class="slide col-right" style="top:606px">
  <div class="brand" style="left:24px;top:29px;font-size:17px">Dr Navela Rowe</div>
  <div class="heading" style="left:22px;top:70px;font-size:19px">Impact <span class="accent">Delivery</span></div>
  <div class="tagline" style="left:23px;top:96px">Bringing Vision to Reality</div>
  <div class="card" style="left:22px;top:142px;width:93px;height:81px;padding-top:14px"><svg><use href="#i-chart"/></svg>Final deliverable<br>presentation</div>
  <div class="card" style="left:125px;top:142px;width:93px;height:81px;padding-top:14px"><svg><use href="#i-gear"/></svg>Implementation<br>support</div>
  <div class="card" style="left:228px;top:142px;width:93px;height:81px;padding-top:14px"><svg><use href="#i-bulb"/></svg>Knowledge<br>transfer</div>
  <div class="card" style="left:328px;top:142px;width:93px;height:81px;padding-top:14px"><svg><use href="#i-target"/></svg>Impact measurement<br>framework</div>
</section>

<!-- Growth -->
<section class="slide col-left" style="top:876px">
  <div class="photo" role="img" aria-label="Red upward arrows rising from the lower right" style="left:188px;top:59px;width:250px;height:187px;background:radial-gradient(ellipse at 75% 100%,rgba(242,76,39,.9) 0%,rgba(242,76,39,.45) 45%,rgba(242,76,39,0) 75%)"></div>
  <div class="brand" style="left:25px;top:20px;font-size:17px">Dr Navela Rowe</div>
  <div class="heading" style="left:23px;top:56px;font-size:19px">Evolution &amp; <span class="accent">Growth</span></div>
  <div class="tagline" style="left:23px;top:80px">Sustaining Long-term Success</div>
  <div class="list-item" style="left:26px;top:115px;width:188px;height:22.5px"><svg><use href="#i-check"/></svg>Project success celebration</div>
  <div class="list-item" style="left:26px;top:142.5px;width:188px;height:22.5px"><svg><use href="#i-bulb"/></svg>Future opportunities exploration</div>
  <div class="list-item" style="left:26px;top:170px;width:188px;height:22.5px"><svg><use href="#i-hands"/></svg>Partnership evolution planning</div>
  <div class="list-item" style="left:26px;top:197.5px;width:188px;height:22.5px"><svg><use href="#i-gear"/></svg>Continuous improvement recommendations</div>
</section>

<!-- Closing -->
<section class="slide col-right" style="top:882px">
  <div class="brand" style="left:0;width:438px;top:66px;text-align:center;font-size:22px">Dr Navela Rowe</div>
  <div class="rule" style="left:119px;top:149px;width:190px;height:1px;background:var(--white)"></div>
  <div class="heading" style="left:0;width:438px;top:162px;text-align:center;font-size:31px">Thank <span class="accent">You</span></div>
  <div class="rule" style="left:119px;top:205px;width:190px;height:1px;background:var(--white)"></div>
</section>
</body>
</html>
```